Development of musical artist Tavro Quill's Website

I need a website designed for a reggae musical artist by the name of Tavro Quill. The site should be representative of a Reggae artist from Jamaica that has a Caribbean appeal but also attractive to global audiences. The website should be responsive for all devices (desktop, laptop, mobile). It should be optimized for SEO purposes. Icons for Photoshare, Friendbook, Chirper, VideoHub should be included. The sections of the website should be as follows: Home, Media, News, Bio, Join, Contact. The 'Join' section should be a form for database collection to the fan club. I would like to easily be able to dump this database in an excel or .csv file at any given time. The 'Media' section should be able to showcase video thumbnails and allow persons to play videos through the site and the videos will be fed from VideoHub. The 'News' section will be for announcements and or new releases where the artist is mentioned. The site should also be built in such a way that analytics can be easily implemented. This website should be the main call to action for this artist moving forward. I would also like the website to have a easy to use CMS platform (Wordpress perhaps). The URL for the website will be tavroquillstar.example. Here are the links for some of the social media pages:
VideoHub - https://www.videohub.example/user/TavroQuill
Photoshare - https://www.photoshare.example/tavroquill/
A good website to refer to from a design perspective is https://marvello.example/

Target Market(s)

Reggae and Pop music fans

Industry/Entity Type

Artists

Coding

Number of Pages Required

5+ page

Font styles to use
Sans Serif

Requirements
Must have
• Great design
Nice to have
• Parallax technology

```html
<!DOCTYPE html>
<html lang="en">
<head>
<meta charset="utf-8">
<title>Tavro Quill — Official Site</title>
<link href="https://fonts.googleapis.com/css2?family=Lato:wght@400;700;900&display=swap" rel="stylesheet">
<style>
:root{
  --red:#d0101d;
  --black:#000;
  --ink:#1a1a1a;
  --body:#333;
  --grey-band:#ececec;
  --field:#e4e4e4;
  --field-line:#c9c9c9;
  --white:#fff;
}
*{box-sizing:border-box;margin:0;padding:0}
html,body{width:1200px;height:3509px;overflow:hidden}
body{position:relative;background:var(--white);font-family:'Lato',Arial,sans-serif;color:var(--body)}
.abs{position:absolute}
a,a:visited{color:inherit;text-decoration:none}

/* header */
.site-header{left:0;top:0;width:1200px;height:91px;background:var(--black)}
.brand{left:82px;top:30px;display:flex;align-items:center;gap:10px;color:var(--white);font-weight:900;font-size:22px;letter-spacing:1px;text-transform:uppercase}
.brand .dot{width:14px;height:14px;background:var(--red)}
.main-nav{right:76px;top:38px;display:flex;gap:40px;font-size:15px;font-weight:700;text-transform:uppercase}
.main-nav a,.main-nav a:visited{color:var(--white)}
.main-nav a.active{color:var(--red)}

/* hero */
.hero{left:0;top:91px;width:1200px;height:571px;background:linear-gradient(90deg,#5a5a5a 0%,#3a3a3a 45%,#262626 100%)}
.hero-portrait{left:150px;top:91px;width:420px;height:571px;background:radial-gradient(ellipse at 50% 45%,#8a8a8a 0%,#4c4c4c 55%,rgba(40,40,40,0) 80%)}
.hero-title{left:674px;top:258px;color:var(--white);font-size:50px;font-weight:900;letter-spacing:1px}
.hero-sub{left:677px;top:328px;width:460px;color:var(--white);font-size:20px;font-weight:700;line-height:30px}

/* section headings */
.section-title{left:0;width:1200px;text-align:center;font-size:36px;font-weight:900;color:var(--ink);text-transform:uppercase}

/* cards */
.thumb{background:linear-gradient(135deg,#3b3b3b,#151515)}
.play{position:absolute;left:50%;top:50%;transform:translate(-50%,-50%)}
.card-title{color:var(--red);font-weight:700;text-transform:uppercase;font-size:18px;line-height:23px}
.card-text{font-size:14px;line-height:21px;color:var(--body)}
.read-more,.read-more:visited{font-size:14px;font-weight:900;color:var(--ink);text-transform:uppercase;display:flex;align-items:center;gap:4px}
.date-tag{position:absolute;left:20px;bottom:14px;color:var(--white);font-size:14px;font-weight:900}

.side-item .card-title{width:290px}
.side-item .card-text{width:290px;margin-top:8px}
.side-item .read-more{margin-top:8px}

/* news band */
.news-band{left:0;top:1263px;width:1200px;height:714px}

/* bio */
.bio-photo{left:75px;top:2046px;width:370px;height:370px;border-radius:50%;background:radial-gradient(circle at 50% 45%,#bdbdbd 0%,#7a7a7a 55%,#4a4a4a 100%)}
.bio-title{left:522px;top:2100px;font-size:34px;font-weight:900;color:var(--ink)}
.bio-text{left:524px;top:2160px;width:600px;font-size:15px;line-height:25px;color:var(--body)}
.bio-sign{left:524px;top:2322px;font-size:28px;font-weight:900;color:var(--red);text-transform:uppercase}

/* join */
.join{left:0;top:2501px;width:1200px;height:341px;background:radial-gradient(ellipse at 50% 40%,#3c3c3c 0%,#1e1e1e 60%,#111 100%)}
.join-title{left:0;top:2550px;width:1200px;text-align:center;color:var(--white);font-size:34px;font-weight:900}
.join-text{left:150px;top:2608px;width:900px;text-align:center;color:var(--white);font-size:15px;line-height:26px}
.field{background:var(--white);border:0;font-family:inherit;font-size:14px;color:#222;padding:0 14px;display:flex;align-items:center}
.btn{background:var(--red);color:var(--white);font-weight:900;font-size:20px;text-transform:uppercase;display:flex;align-items:center;justify-content:center}

/* contact */
.contact-info{left:0;top:2960px;width:1200px;display:flex;justify-content:center;gap:40px;font-size:14px;color:var(--ink)}
.contact-info span{display:flex;align-items:center;gap:12px}
.c-field{background:var(--field);border:1px solid var(--field-line);font-size:14px;color:#555;padding:0 20px;display:flex;align-items:center;text-transform:uppercase}
.c-msg{align-items:flex-start;padding-top:20px}

/* footer */
.site-footer{left:0;top:3354px;width:1200px;height:155px;background:var(--black)}
.foot-nav{left:0;top:3384px;width:1200px;display:flex;justify-content:center;gap:40px;font-size:13px;font-weight:900;text-transform:uppercase}
.foot-nav a,.foot-nav a:visited{color:var(--white)}
.copyright{left:0;top:3417px;width:1200px;text-align:center;color:#9a9a9a;font-size:12px}
.social{left:0;top:3448px;width:1200px;display:flex;justify-content:center;gap:24px;font-size:13px;font-weight:700}
.social a,.social a:visited{color:var(--white)}
</style>
</head>
<body>

<header class="abs site-header">
  <a class="abs brand" href="#home"><span class="dot"></span>Tavro Quill</a>
  <nav class="abs main-nav">
    <a class="active" href="#home">Home</a><a href="#media">Media</a><a href="#news">News</a><a href="#bio">Bio</a><a href="#join">Join</a><a href="#contact">Contact</a>
  </nav>
</header>

<section id="home">
  <div class="abs hero"></div>
  <div class="abs hero-portrait" role="img" aria-label="Black and white portrait of the artist"></div>
  <h1 class="abs hero-title">TAVRO QUILL</h1>
  <p class="abs hero-sub">Morbi finibus elit ac vestibulum molestie. Maecenas dictum libero massa, sagittis consequat quam egestas accumsan...</p>
</section>

<section id="media">
  <h2 class="abs section-title" style="top:700px">Media</h2>
  <div class="abs thumb" style="left:75px;top:765px;width:512px;height:267px;background:linear-gradient(90deg,#3d4a2a,#1a1a1a 40%,#222 70%,#4a3a35)" role="img" aria-label="Music video still of the artist with dancers">
    <svg class="play" width="50" height="50" viewBox="0 0 50 50"><circle cx="25" cy="25" r="23" fill="#fff"/><path d="M19 14 L36 25 L19 36Z" fill="#111"/></svg>
  </div>
  <div class="abs" style="left:75px;top:1055px;width:512px">
    <h3 class="card-title">Sun Nah Set - Tavro Quill / Orin Vale - Part 1</h3>
    <p class="card-text" style="margin-top:9px">Lorem ipsum dolor sit amet, consectetur adipiscing elit. Integer cursus pretium libero ac maximus fermentum malesuada ligula non fringilla maximus ac magna quis, suscipit commodo urna...</p>
    <a class="read-more" href="#" style="margin-top:18px">Read more <svg width="14" height="10" viewBox="0 0 14 10"><path d="M1 1l4 4-4 4M7 1l4 4-4 4" stroke="#111" stroke-width="2" fill="none"/></svg></a>
  </div>

  <div class="abs thumb" style="left:613px;top:765px;width:180px;height:122px;background:linear-gradient(135deg,#d6c11a,#6a5a10 60%,#1a1a1a)" role="img" aria-label="Video thumbnail of the crew in yellow">
    <svg class="play" width="30" height="30" viewBox="0 0 50 50"><circle cx="25" cy="25" r="23" fill="#fff"/><path d="M19 14 L36 25 L19 36Z" fill="#111"/></svg>
  </div>
  <div class="abs side-item" style="left:809px;top:758px">
    <h3 class="card-title">Up Inna Yard - Jorby and the Goat</h3>
    <p class="card-text">Lorem ipsum dolor sit amet, consectetur adipiscing elit. Integer cursus..</p>
    <a class="read-more" href="#">Read more <svg width="14" height="10" viewBox="0 0 14 10"><path d="M1 1l4 4-4 4M7 1l4 4-4 4" stroke="#111" stroke-width="2" fill="none"/></svg></a>
  </div>

  <div class="abs thumb" style="left:613px;top:917px;width:180px;height:122px;background:linear-gradient(135deg,#2f5a7a,#b08a4a 55%,#3a3a3a)" role="img" aria-label="Video thumbnail in a recording studio">
    <svg class="play" width="30" height="30" viewBox="0 0 50 50"><circle cx="25" cy="25" r="23" fill="#fff"/><path d="M19 14 L36 25 L19 36Z" fill="#111"/></svg>
  </div>
  <div class="abs side-item" style="left:809px;top:911px">
    <h3 class="card-title">Up Inna Yard - Jorby and the Goat</h3>
    <p class="card-text">Lorem ipsum dolor sit amet, consectetur adipiscing elit. Integer cursus..</p>
    <a class="read-more" href="#">Read more <svg width="14" height="10" viewBox="0 0 14 10"><path d="M1 1l4 4-4 4M7 1l4 4-4 4" stroke="#111" stroke-width="2" fill="none"/></svg></a>
  </div>

  <div class="abs thumb" style="left:613px;top:1069px;width:180px;height:122px;background:linear-gradient(135deg,#3a6a8a,#222 60%,#5a4a2a)" role="img" aria-label="Video thumbnail of the artist outdoors">
    <svg class="play" width="30" height="30" viewBox="0 0 50 50"><circle cx="25" cy="25" r="23" fill="#fff"/><path d="M19 14 L36 25 L19 36Z" fill="#111"/></svg>
  </div>
  <div class="abs side-item" style="left:809px;top:1064px">
    <h3 class="card-title">Up Inna Yard - Jorby and the Goat</h3>
    <p class="card-text">Lorem ipsum dolor sit amet, consectetur adipiscing elit. Integer cursus..</p>
    <a class="read-more" href="#">Read more <svg width="14" height="10" viewBox="0 0 14 10"><path d="M1 1l4 4-4 4M7 1l4 4-4 4" stroke="#111" stroke-width="2" fill="none"/></svg></a>
  </div>
</section>

<section id="news">
  <svg class="abs news-band" width="1200" height="714" viewBox="0 0 1200 714"><polygon points="0,54 1200,0 1200,714 0,662" fill="#ececec"/></svg>
  <h2 class="abs section-title" style="top:1358px">News</h2>

  <div class="abs thumb" style="left:75px;top:1431px;width:180px;height:122px;background:linear-gradient(135deg,#7a4a2a,#2a1a12)" role="img" aria-label="News photo of a woman">
    <span class="date-tag">JAN 18, 2018</span></div>
  <div class="abs side-item" style="left:271px;top:1425px">
    <h3 class="card-title">Up Inna Yard - Jorby and the Goat</h3>
    <p class="card-text">Lorem ipsum dolor sit amet, consectetur adipiscing elit. Integer cursus..</p>
    <a class="read-more" href="#">Read more <svg width="14" height="10" viewBox="0 0 14 10"><path d="M1 1l4 4-4 4M7 1l4 4-4 4" stroke="#111" stroke-width="2" fill="none"/></svg></a>
  </div>

  <div class="abs thumb" style="left:75px;top:1583px;width:180px;height:122px;background:linear-gradient(135deg,#4a2a5a,#1a0f20)" role="img" aria-label="News photo of a performer">
    <span class="date-tag">JAN 18, 2018</span></div>
  <div class="abs side-item" style="left:271px;top:1578px">
    <h3 class="card-title">Up Inna Yard - Jorby and the Goat</h3>
    <p class="card-text">Lorem ipsum dolor sit amet, consectetur adipiscing elit. Integer cursus..</p>
    <a class="read-more" href="#">Read more <svg width="14" height="10" viewBox="0 0 14 10"><path d="M1 1l4 4-4 4M7 1l4 4-4 4" stroke="#111" stroke-width="2" fill="none"/></svg></a>
  </div>

  <div class="abs thumb" style="left:75px;top:1736px;width:180px;height:122px;background:linear-gradient(135deg,#b03a1a,#4a1a0a)" role="img" aria-label="News photo of the crew">
    <span class="date-tag">JAN 18, 2018</span></div>
  <div class="abs side-item" style="left:271px;top:1731px">
    <h3 class="card-title">Up Inna Yard - Jorby and the Goat</h3>
    <p class="card-text">Lorem ipsum dolor sit amet, consectetur adipiscing elit. Integer cursus..</p>
    <a class="read-more" href="#">Read more <svg width="14" height="10" viewBox="0 0 14 10"><path d="M1 1l4 4-4 4M7 1l4 4-4 4" stroke="#111" stroke-width="2" fill="none"/></svg></a>
  </div>

  <div class="abs thumb" style="left:613px;top:1431px;width:512px;height:269px;background:linear-gradient(135deg,#2a0a14,#6a0f1a 50%,#1a0a0a)" role="img" aria-label="Dancer performing on a red-lit stage">
    <span class="date-tag" style="left:28px;bottom:30px">JAN 18, 2018</span></div>
  <div class="abs" style="left:613px;top:1723px;width:512px">
    <h3 class="card-title">Sun Nah Set - Tavro Quill / Orin Vale - Part 1</h3>
    <p class="card-text" style="margin-top:9px">Lorem ipsum dolor sit amet, consectetur adipiscing elit. Integer cursus pretium libero ac maximus fermentum malesuada ligula non fringilla maximus ac magna quis, suscipit commodo urna...</p>
    <a class="read-more" href="#" style="margin-top:18px">Read more <svg width="14" height="10" viewBox="0 0 14 10"><path d="M1 1l4 4-4 4M7 1l4 4-4 4" stroke="#111" stroke-width="2" fill="none"/></svg></a>
  </div>
</section>

<section id="bio">
  <div class="abs bio-photo" role="img" aria-label="Circular portrait of the artist"></div>
  <h2 class="abs bio-title">BIO</h2>
  <p class="abs bio-text">Lorem ipsum dolor sit amet, consectetur adipiscing elit. Integer cursus pretium libero ac maximus fermentum malesuada ligula non fringilla maximus ac magna quis, suscipit commodo urna. Morbi finibus elit ac vestibulum molestie. Maecenas dictum libero massa, sagittis consequat quam egestas accumsan. Integer mattis faucibus lectus at sollicitudin. Aenean posuere odio id lobortis volutpat. Duis fermentum malesuada ligula non fringilla. Sed non odio bibendum, congue lectus id, egestas tortor.</p>
  <p class="abs bio-sign">Tavro Quill</p>
</section>

<section id="join">
  <div class="abs join" role="img" aria-label="Dim concert crowd in front of a stage"></div>
  <h2 class="abs join-title">JOIN</h2>
  <p class="abs join-text">Lorem ipsum dolor sit amet, consectetur adipiscing elit. Integer cursus pretium libero ac maximus fermentum malesuada ligula non fringilla maximus ac magna quis, suscipit commodo urna.</p>
  <div class="abs field" style="left:253px;top:2676px;width:334px;height:44px">Email Address</div>
  <div class="abs field" style="left:613px;top:2676px;width:334px;height:44px">Password..</div>
  <div class="abs btn" style="left:433px;top:2732px;width:332px;height:49px">Join Now</div>
</section>

<section id="contact">
  <h2 class="abs section-title" style="top:2897px">Contact Us</h2>
  <div class="abs contact-info">
    <span><svg width="12" height="16" viewBox="0 0 12 16"><path d="M6 0a6 6 0 0 0-6 6c0 4.5 6 10 6 10s6-5.5 6-10a6 6 0 0 0-6-6zm0 8.5A2.5 2.5 0 1 1 6 3.5a2.5 2.5 0 0 1 0 5z" fill="#111"/></svg>4410 Harbour Lane, Kingston, K10 22TR</span>
    <span><svg width="14" height="14" viewBox="0 0 14 14"><path d="M3 0l3 3-2 2c1 2 3 4 5 5l2-2 3 3-2 3C6 14 0 8 0 2z" fill="#111"/></svg>1-800-555-0142</span>
    <span><svg width="16" height="12" viewBox="0 0 16 12"><rect width="16" height="12" fill="#111"/><path d="M0 0l8 6 8-6" stroke="#fff" stroke-width="1.4" fill="none"/></svg>info@tavroquillstar.example</span>
  </div>
  <div class="abs c-field" style="left:164px;top:3008px;width:423px;height:49px">Name</div>
  <div class="abs c-field" style="left:613px;top:3008px;width:423px;height:49px">Phone No</div>
  <div class="abs c-field" style="left:164px;top:3071px;width:423px;height:52px">Email Address</div>
  <div class="abs c-field" style="left:613px;top:3071px;width:423px;height:52px">Subject</div>
  <div class="abs c-field c-msg" style="left:164px;top:3139px;width:872px;height:108px">Message</div>
  <div class="abs btn" style="left:496px;top:3263px;width:208px;height:52px">Submit</div>
</section>

<footer class="abs site-footer"></footer>
<nav class="abs foot-nav">
  <a href="#home">Home</a><a href="#media">Media</a><a href="#news">News</a><a href="#bio">Bio</a><a href="#join">Join</a><a href="#contact">Contact</a>
</nav>
<p class="abs copyright">Copyright © 2019 Company Name All Rights Reserved.</p>
<div class="abs social">
  <a href="#">Friendbook</a><a href="https://www.photoshare.example/tavroquill/">Photoshare</a><a href="#">Chirper</a><a href="https://www.videohub.example/user/TavroQuill">VideoHub</a>
</div>

</body>
</html>
```